Revise Three Graphics for Company Careers website.

We have a need to find an alternative artistic approach to revising three graphics currently used on a growing companies careers/job website.
- The new art for attached graphics (named graphic #1, #2, and #3) should be clean, professional and easy to read.
- The art representing these three pieces should share common artistic elements and not necessarily look like three differently branded pieces.
- The careers site is shared between two related companies, so the colors used should complement the colors of two companies (whose logos are attached).
- Logos can be used as knock-outs if needed.
Note: Graphic #3 (currently a set of boxes 2x3) needs two additional boxes with the following copy:
- Art and Science of Communication
- Supervising 101
Lastly, Graphic #4 we need to be put into the same color font used in the two company logos. That's it!

```html
<!DOCTYPE html>
<html lang="en">
<head>
<meta charset="utf-8">
<title>The Forge Technology Platform</title>
<link rel="stylesheet" href="https://fonts.googleapis.com/css2?family=Roboto+Condensed:wght@300;400;700&display=swap">
<style>
  :root {
    --navy: #1f3f7d;
    --white: #ffffff;
    --orange: #f5a31a;
    --orange-deep: #ee8a1c;
    --yellow: #fdd319;
    --yellow-deep: #f6b81a;
    --lime: #b4cf2e;
    --lime-deep: #7fae22;
    --green: #99c32a;
    --green-deep: #6d9c1d;
    --blue: #2f9fdb;
    --blue-deep: #1f7fc4;
    --sky: #3cb6e8;
    --sky-deep: #2496d6;
    --red: #e8303d;
    --red-deep: #b51e2a;
  }
  html, body {
    margin: 0;
    padding: 0;
    overflow: hidden;
    background: var(--white);
  }
  .platform {
    position: relative;
    width: 1200px;
    height: 927px;
    overflow: hidden;
    background: var(--white);
    font-family: "Roboto Condensed", Arial, sans-serif;
  }
  .platform__wheel {
    position: absolute;
    left: 0;
    top: 0;
  }
  .segment-label {
    font-family: "Roboto Condensed", Arial, sans-serif;
    font-weight: 700;
    font-size: 20px;
    fill: var(--white);
    text-anchor: middle;
  }
  .hub-title {
    font-family: "Roboto Condensed", Arial, sans-serif;
    fill: var(--navy);
    text-anchor: middle;
    font-size: 38px;
  }
  .hub-title--light { font-weight: 300; }
  .hub-title--bold { font-weight: 700; }
  .company-name {
    position: absolute;
    bottom: 52px;
    margin: 0;
    color: var(--navy);
    font-weight: 400;
    font-size: 38px;
    letter-spacing: 1px;
  }
  .company-name--left { left: 46px; }
  .company-name--right { right: 46px; }
</style>
</head>
<body>
<main class="platform">
  <svg class="platform__wheel" width="1200" height="927" viewBox="0 0 1200 927" aria-label="Wheel of nine departments around the Forge Technology Platform">
    <defs>
      <linearGradient id="fill-orange" x1="0" y1="0" x2="1" y2="0"><stop offset="0" stop-color="var(--orange-deep)"/><stop offset="1" stop-color="var(--orange)"/></linearGradient>
      <linearGradient id="fill-yellow" x1="0" y1="0" x2="1" y2="0"><stop offset="0" stop-color="var(--yellow-deep)"/><stop offset="1" stop-color="var(--yellow)"/></linearGradient>
      <linearGradient id="fill-lime" x1="0" y1="0" x2="1" y2="0"><stop offset="0" stop-color="var(--lime)"/><stop offset="1" stop-color="var(--lime-deep)"/></linearGradient>
      <linearGradient id="fill-green" x1="0" y1="0" x2="1" y2="0"><stop offset="0" stop-color="var(--green)"/><stop offset="1" stop-color="var(--green-deep)"/></linearGradient>
      <linearGradient id="fill-blue" x1="0" y1="0" x2="1" y2="0"><stop offset="0" stop-color="var(--blue)"/><stop offset="1" stop-color="var(--blue-deep)"/></linearGradient>
      <linearGradient id="fill-sky" x1="0" y1="0" x2="1" y2="0"><stop offset="0" stop-color="var(--sky)"/><stop offset="1" stop-color="var(--sky-deep)"/></linearGradient>
      <linearGradient id="fill-red" x1="0" y1="0" x2="1" y2="0"><stop offset="0" stop-color="var(--red)"/><stop offset="1" stop-color="var(--red-deep)"/></linearGradient>
      <path id="segment" d="M116.5 -62 L247.4 -61.7 L366.5 -133.4 A390 390 0 0 1 366.5 133.4 L229.2 111.8 L129.1 27.4 A132 132 0 0 0 116.5 -62 Z"/>
    </defs>

    <g class="wheel" transform="translate(600 446)">
      <use href="#segment" class="segment segment--analytical" fill="url(#fill-orange)" transform="rotate(-91)"/>
      <use href="#segment" class="segment segment--regulatory" fill="url(#fill-yellow)" transform="rotate(-51)"/>
      <use href="#segment" class="segment segment--manufacturing" fill="url(#fill-lime)" transform="rotate(-11)"/>
      <use href="#segment" class="segment segment--fabrication" fill="url(#fill-green)" transform="rotate(29)"/>
      <use href="#segment" class="segment segment--product" fill="url(#fill-blue)" transform="rotate(69)"/>
      <use href="#segment" class="segment segment--biology" fill="url(#fill-sky)" transform="rotate(109)"/>
      <use href="#segment" class="segment segment--business" fill="url(#fill-blue)" transform="rotate(149)"/>
      <use href="#segment" class="segment segment--admin" fill="url(#fill-red)" transform="rotate(189)"/>
      <use href="#segment" class="segment segment--ip" fill="url(#fill-red)" transform="rotate(229)"/>
      <circle class="wheel__hub" r="132" fill="var(--white)"/>
    </g>

    <g class="segment-labels">
      <text class="segment-label" x="593" y="158">ANALYTICAL</text>
      <text class="segment-label" x="783" y="176">REGULATORY<tspan x="783" dy="24">&amp; QUALITY</tspan></text>
      <text class="segment-label" x="852" y="354">MANUFACTORING<tspan x="852" dy="24">DEVELOPMENT</tspan><tspan x="852" dy="24">&amp; OPERATIONS</tspan></text>
      <text class="segment-label" x="858" y="536">PARTICLE<tspan x="858" dy="24">FABRICATION</tspan></text>
      <text class="segment-label" x="753" y="673">PRODUCT<tspan x="753" dy="24">DEVELOPMENT</tspan></text>
      <text class="segment-label" x="555" y="708">BIOLOGY<tspan x="555" dy="24">&amp; IMMUNITY</tspan></text>
      <text class="segment-label" x="393" y="576">BUSINESS<tspan x="393" dy="24">DEVELOPMENT</tspan><tspan x="393" dy="24">&amp; STRATEGY</tspan></text>
      <text class="segment-label" x="342" y="374">GENERAL<tspan x="342" dy="24">ADMIN, HR</tspan><tspan x="342" dy="24">&amp; FINANCE</tspan></text>
      <text class="segment-label" x="412" y="217">INTELLECTUAL<tspan x="412" dy="24">PROPERTY</tspan></text>
    </g>

    <g class="hub-title-group">
      <text class="hub-title hub-title--light" x="600" y="366">THE</text>
      <text class="hub-title hub-title--bold" x="600" y="410">FORGE</text>
      <text class="hub-title hub-title--bold" x="600" y="456">TECHNOLOGY</text>
      <text class="hub-title hub-title--light" x="600" y="502">PLATFORM</text>
    </g>
  </svg>

  <p class="company-name company-name--left">Verolia Technologies</p>
  <p class="company-name company-name--right">Calora Therapeutics</p>
</main>
</body>
</html>
```